We are a recruitment company based in Norwich/Cambridge England.
I have included our company logo which we want to remain the same.

What we are looking for is a new creative Business card which will really stand out!!

Contact Information for Business Card

Harriet Dunmore
email: Harriet@plavex.co.uk
Address: Brackwell House
Fenmoor Enterprise Park
Partridge Way
Norwich
QB9 3KX
Tel:01632 960418

```html
<!DOCTYPE html>
<html lang="en">
<head>
<meta charset="utf-8">
<title>Plavex Business Card</title>
<link rel="stylesheet" href="https://fonts.googleapis.com/css2?family=Jost:wght@400;500&family=Open+Sans:wght@600;800&display=swap">
<style>
  :root {
    --stage: #2a2a2b;
    --card-grey: #8e8b91;
    --map-tone: #a09da2;
    --paper: #ffffff;
    --ink: #1f1f21;
    --green: #86c440;
    --band-grey: #8f8c93;
    --faint-green: #e3efd2;
    --pale-text: #f2f2f2;
  }
  * { margin: 0; padding: 0; box-sizing: border-box; }
  html, body { width: 1200px; height: 900px; overflow: hidden; background: var(--stage); }
  .stage { position: relative; width: 1200px; height: 900px; }

  .card {
    position: absolute;
    left: 280px;
    width: 640px;
    height: 366px;
    overflow: hidden;
    box-shadow: 0 14px 30px rgba(0,0,0,0.45);
  }

  /* Back */
  .card-back { top: 50px; background: var(--card-grey); }
  .card-back .world-map {
    position: absolute; inset: 20px 30px 40px 30px;
    background: radial-gradient(ellipse at center, var(--map-tone) 0%, rgba(160,157,162,0.35) 60%, rgba(142,139,145,0) 100%);
    border-radius: 40px;
  }
  .card-back .brand {
    position: absolute; top: 130px; left: 0; right: 0;
    display: flex; align-items: center; justify-content: center; gap: 16px;
  }
  .brand-dot { width: 44px; height: 44px; border-radius: 50%; background: var(--green); }
  .brand-name {
    font-family: "Jost", sans-serif; font-weight: 500; font-size: 56px;
    color: var(--green); letter-spacing: 0.5px; line-height: 1;
  }
  .card-back .brand-name { color: var(--pale-text); }
  .card-back .web {
    position: absolute; bottom: 34px; left: 0; right: 0; text-align: center;
    font-family: "Jost", sans-serif; font-size: 16px; letter-spacing: 4px; color: var(--pale-text);
  }

  /* Front */
  .card-front { top: 470px; background: var(--paper); }
  .holder { position: absolute; top: 34px; left: 40px; color: var(--ink); }
  .holder-name {
    font-family: "Open Sans", sans-serif; font-weight: 800; font-size: 34px;
    letter-spacing: 1.5px; line-height: 1;
  }
  .holder-role {
    margin-top: 4px;
    font-family: "Open Sans", sans-serif; font-weight: 600; font-size: 19px; letter-spacing: 0.5px;
  }
  .card-front .brand {
    position: absolute; top: 120px; right: 40px;
    display: flex; align-items: center; gap: 12px;
  }
  .card-front .brand-dot { background: var(--band-grey); width: 40px; height: 40px; }
  .card-front .brand-name { font-size: 50px; }

  .accent-circle {
    position: absolute; right: 60px; bottom: 40px;
    width: 150px; height: 150px; border-radius: 50%;
    background: var(--faint-green); opacity: 0.8;
  }

  .contact {
    position: absolute; left: 40px; top: 190px;
    font-family: "Jost", sans-serif; color: var(--ink);
  }
  .address { font-size: 17px; line-height: 1.2; margin-bottom: 12px; }
  .contact-list { list-style: none; font-size: 18px; line-height: 1.35; }
  .contact-list li { display: flex; align-items: center; gap: 10px; }
  .contact-list svg { width: 16px; height: 16px; flex: none; }
  .contact-list .accent { color: var(--green); }

  .footer-bands { position: absolute; left: 0; bottom: 0; width: 640px; height: 40px; }
</style>
</head>
<body>
<main class="stage">
  <section class="card card-back" aria-label="Card back">
    <div class="world-map" role="img" aria-label="Faint world map in light grey"></div>
    <div class="brand">
      <span class="brand-dot"></span>
      <span class="brand-name">Plavex</span>
    </div>
    <p class="web">www.plavexsite.com</p>
  </section>

  <section class="card card-front" aria-label="Card front">
    <div class="holder">
      <h1 class="holder-name">HARRIET DUNMORE</h1>
      <p class="holder-role">CEO &amp; FOUNDER</p>
    </div>

    <div class="brand">
      <span class="brand-dot"></span>
      <span class="brand-name">Plavex</span>
    </div>

    <div class="accent-circle" aria-hidden="true"></div>

    <div class="contact">
      <p class="address">Brackwell House Fenmoor Enterprise Park,<br>Partridge Way Norwich, QB9 3KX</p>
      <ul class="contact-list">
        <li>
          <svg viewBox="0 0 16 16" aria-hidden="true"><path d="M3 1.5l3 3-1.6 1.6a8 8 0 0 0 5.5 5.5L11.5 10l3 3-1.8 1.8C7 14.5 1.5 9 1.2 3.3z" fill="#86c440"/></svg>
          01632 960418
        </li>
        <li>
          <svg viewBox="0 0 16 16" aria-hidden="true"><rect x="1" y="3" width="14" height="10" rx="1" fill="#86c440"/><path d="M1.5 3.5L8 9l6.5-5.5" stroke="#fff" stroke-width="1.3" fill="none"/></svg>
          Harriet@plavex.co.uk
        </li>
        <li>
          <svg viewBox="0 0 16 16" aria-hidden="true"><circle cx="9.5" cy="6.5" r="4.8" stroke="#86c440" stroke-width="1.8" fill="none"/><path d="M6 10L1.5 14.5" stroke="#86c440" stroke-width="2" stroke-linecap="round"/></svg>
          <span>www.<span class="accent">plavexsite</span>.com</span>
        </li>
      </ul>
    </div>

    <svg class="footer-bands" viewBox="0 0 640 40" preserveAspectRatio="none" aria-hidden="true">
      <polygon points="0,0 430,14 410,40 0,40" fill="#86c440"/>
      <polygon points="440,14 640,20 640,40 420,40" fill="#8f8c93"/>
    </svg>
  </section>
</main>
</body>
</html>
```